We are a recruitment company based in Norwich/Cambridge England.
I have included our company logo which we want to remain the same.

What we are looking for is a new creative Business card which will really stand out!!

Contact Information for Business Card

Harriet Dunmore
email: Harriet@plavex.co.uk
Address: Brackwell House
Fenmoor Enterprise Park
Partridge Way
Norwich
QB9 3KX
Tel:01632 960418

```html
<!DOCTYPE html>
<html lang="en">
<head>
<meta charset="utf-8">
<title>Plavex Business Card</title>
<link href="https://fonts.googleapis.com/css2?family=Work+Sans:wght@400;500;600&display=swap" rel="stylesheet">
<style>
  :root {
    --backdrop: #1b1b1b;
    --green: #8dc63f;
    --grey: #8a898d;
    --ink: #3a3a3a;
    --white: #ffffff;
  }
  html, body {
    margin: 0;
    padding: 0;
    width: 1200px;
    height: 897px;
    overflow: hidden;
    background: var(--backdrop);
    font-family: "Work Sans", Arial, sans-serif;
  }
  .stage {
    position: relative;
    width: 1200px;
    height: 897px;
  }
  .card {
    position: absolute;
    left: 303px;
    width: 595px;
    height: 338px;
    border-radius: 19px;
    overflow: hidden;
  }
  .card--front { top: 92px; background: var(--white); }
  .card--back { top: 469px; background: var(--green); }

  .brand {
    position: absolute;
    display: flex;
    flex-direction: column;
  }
  .brand__row {
    display: flex;
    align-items: center;
  }
  .brand__dot {
    border-radius: 50%;
    flex: none;
  }
  .brand__name {
    font-weight: 500;
    line-height: 1;
    letter-spacing: -0.5px;
  }
  .brand__tagline {
    font-weight: 500;
    text-transform: none;
  }

  .card--front .brand { left: 40px; top: 153px; }
  .card--front .brand__dot { width: 40px; height: 40px; background: var(--green); margin-right: 10px; }
  .card--front .brand__name { font-size: 42px; color: var(--grey); }
  .card--front .brand__tagline { font-size: 7.5px; letter-spacing: 2.6px; color: var(--grey); margin: 2px 0 0 51px; }

  .divider {
    position: absolute;
    left: 312px;
    top: 92px;
    width: 2px;
    height: 152px;
    background: var(--green);
  }
  .contact {
    position: absolute;
    left: 342px;
    top: 88px;
    color: var(--ink);
    font-size: 14.5px;
    letter-spacing: 0.6px;
    line-height: 19px;
  }
  .contact__name {
    margin: 0;
    font-size: 23px;
    font-weight: 500;
    color: var(--green);
    line-height: 28px;
    letter-spacing: 0.4px;
  }
  .contact__role { margin: 0 0 8px; }
  .contact__address { margin: 0 0 8px; font-style: normal; }
  .contact__list { list-style: none; margin: 0; padding: 0; }
  .contact__item { display: flex; align-items: center; }
  .contact__icon { width: 10px; height: 10px; margin-right: 10px; flex: none; }
  .accent { color: var(--green); }

  .band { position: absolute; left: 0; bottom: 0; }

  .card--back .brand { left: 50%; top: 118px; transform: translateX(-50%); align-items: flex-end; }
  .card--back .brand__dot { width: 60px; height: 60px; background: var(--white); margin-right: 14px; }
  .card--back .brand__name { font-size: 60px; color: var(--white); }
  .card--back .brand__tagline { font-size: 10px; letter-spacing: 4px; color: var(--white); margin-top: 4px; }
  .back__url {
    position: absolute;
    left: 0;
    right: 0;
    top: 296px;
    text-align: center;
    color: var(--white);
    font-size: 14px;
    letter-spacing: 1px;
  }
</style>
</head>
<body>
<main class="stage">
  <section class="card card--front">
    <div class="brand">
      <div class="brand__row">
        <span class="brand__dot"></span>
        <span class="brand__name">Plavex</span>
      </div>
      <span class="brand__tagline">Technology Recruitment</span>
    </div>

    <div class="divider"></div>

    <div class="contact">
      <h1 class="contact__name">Harriet Dunmore</h1>
      <p class="contact__role">Founder</p>
      <address class="contact__address">Brackwell House, Partridge Way<br>Fenmoor Enterprise Park, QB9 3KX</address>
      <ul class="contact__list">
        <li class="contact__item">
          <svg class="contact__icon" viewBox="0 0 10 10"><path d="M2 0.8 L3.6 0.8 L4.2 3 L3 3.8 Q3.8 6 6 7 L6.8 5.8 L9 6.4 L9 8 Q8.5 9.2 7 9 Q1.5 8 1 2.5 Q1 1 2 0.8 Z" fill="var(--green)"/></svg>
          01632 960418
        </li>
        <li class="contact__item">
          <svg class="contact__icon" viewBox="0 0 10 10"><rect x="0.8" y="2" width="8.4" height="6" fill="none" stroke="var(--green)" stroke-width="1"/><path d="M0.8 2 L5 5.4 L9.2 2" fill="none" stroke="var(--green)" stroke-width="1"/></svg>
          Harriet@plavex.co.uk
        </li>
        <li class="contact__item">
          <svg class="contact__icon" viewBox="0 0 10 10"><circle cx="5" cy="5" r="4.2" fill="none" stroke="var(--green)" stroke-width="0.9"/><ellipse cx="5" cy="5" rx="1.8" ry="4.2" fill="none" stroke="var(--green)" stroke-width="0.8"/><path d="M0.8 5 H9.2 M1.5 3 H8.5 M1.5 7 H8.5" stroke="var(--green)" stroke-width="0.7"/></svg>
          www.<span class="accent">plavex</span>.co.uk
        </li>
      </ul>
    </div>

    <svg class="band" width="595" height="27" viewBox="0 0 595 27">
      <rect x="0" y="14" width="312" height="13" fill="var(--grey)"/>
      <polygon points="302,27 330,0 595,0 595,27" fill="var(--white)"/>
      <polygon points="306,27 333,0 595,0 595,27" fill="var(--green)"/>
    </svg>
  </section>

  <section class="card card--back">
    <div class="brand">
      <div class="brand__row">
        <span class="brand__dot"></span>
        <div>
          <span class="brand__name">Plavex</span>
        </div>
      </div>
      <span class="brand__tagline">Technology Recruitment</span>
    </div>
    <p class="back__url">www.plavex.co.uk</p>
  </section>
</main>
</body>
</html>
```